Book "Under Quiet Skies"

The cover SHOULD NOT INCLUDE Dorvane Spire and baguette (French bread)
Cover for the book: "Sous les Ciels Calmes" (the title is in French)
Size: 21 x 27cm
Author: Association of coastal painters & Foundation of the northern mountain guides
Publisher (at the bottom of the cover): Editions Marvelle

The book is intended to show that France and its culture can please to teenagers (16 - 20 years old), ie:
- story
- villages, monuments, castles, Porte de Valmirel
- French language, literature
- French national symbol (a cockerel)
- Army
- sport and sport for the disabled
- Foreigners living in France
- art of living

Besoin de plus de jours pour examiner

Waiting for a meeting of the editors, April 14th.

youngpeople

Book

• Dorvane Spire, wand

```html
<!DOCTYPE html>
<html lang="fr">
<head>
<meta charset="utf-8">
<title>Sous les Ciels Calmes — Editions Marvelle</title>
<link rel="stylesheet" href="https://fonts.googleapis.com/css2?family=Allura&family=Marcellus&family=Lato:wght@300&display=swap">
<style>
  :root {
    --paper: #ffffff;
    --ink: #1d1d1f;
    --header-ink: #55555a;
    --title-red: #e8492f;
    --title-blue: #2b3596;
    --collage-blue: #3b2fd4;
    --collage-violet: #6a5fc8;
    --collage-grey: #c4c4cc;
    --collage-rose: #e9a0a0;
    --collage-red: #d9383c;
  }
  * { margin: 0; padding: 0; box-sizing: border-box; }
  html, body { width: 933px; height: 1200px; overflow: hidden; background: var(--paper); }
  .cover {
    position: relative;
    width: 933px;
    height: 1200px;
    background: var(--paper);
    overflow: hidden;
  }
  .authors {
    position: absolute;
    top: 40px;
    left: 0;
    width: 100%;
    text-align: center;
    font-family: "Marcellus", serif;
    font-size: 17px;
    letter-spacing: 1.6px;
    line-height: 30px;
    color: var(--header-ink);
    text-transform: uppercase;
  }
  .collage {
    position: absolute;
    inset: 0;
    width: 933px;
    height: 1200px;
  }
  .title {
    position: absolute;
    left: 0;
    top: 0;
    width: 100%;
    font-family: "Allura", cursive;
    font-weight: 400;
    text-shadow: 2px 3px 4px rgba(0,0,0,0.18);
  }
  .title-line {
    position: absolute;
    white-space: nowrap;
    line-height: 1;
  }
  .title-line--lead {
    left: 160px;
    top: 175px;
    font-size: 140px;
    color: var(--title-red);
  }
  .title-line--main {
    left: 215px;
    top: 300px;
    font-size: 132px;
    color: var(--title-blue);
  }
  .flourish {
    position: absolute;
    inset: 0;
    width: 933px;
    height: 1200px;
    pointer-events: none;
  }
  .publisher {
    position: absolute;
    left: 0;
    bottom: 36px;
    width: 100%;
    text-align: center;
    font-family: "Lato", sans-serif;
    font-weight: 300;
    font-size: 42px;
    color: var(--ink);
  }
</style>
</head>
<body>
<main class="cover">
  <p class="authors">Association des peintres côtiers &amp;<br>Fondation des guides de montagne du nord</p>

  <svg class="collage" viewBox="0 0 933 1200" role="img"
       aria-label="Photo collage: a young dancer leaping with arms spread in a blue hoodie, in front of the Porte de Valmirel, a glass pyramid, a cockerel statue, supporters waving a flag, a soldier, a castle and an island abbey, tinted blue, white and red">
    <defs>
      <linearGradient id="tricolour" x1="0" y1="0" x2="1" y2="0">
        <stop offset="0" stop-color="var(--collage-blue)"/>
        <stop offset="0.3" stop-color="var(--collage-violet)"/>
        <stop offset="0.52" stop-color="var(--collage-grey)"/>
        <stop offset="0.76" stop-color="var(--collage-rose)"/>
        <stop offset="1" stop-color="var(--collage-red)"/>
      </linearGradient>
      <linearGradient id="fade-top" x1="0" y1="0" x2="0" y2="1">
        <stop offset="0" stop-color="#fff" stop-opacity="0"/>
        <stop offset="0.3" stop-color="#fff" stop-opacity="0.75"/>
        <stop offset="0.6" stop-color="#fff" stop-opacity="1"/>
        <stop offset="1" stop-color="#fff" stop-opacity="1"/>
      </linearGradient>
      <radialGradient id="fade-sides" cx="0.5" cy="0.75" r="0.72">
        <stop offset="0.6" stop-color="#fff" stop-opacity="1"/>
        <stop offset="1" stop-color="#fff" stop-opacity="0.35"/>
      </radialGradient>
      <mask id="soft-edge">
        <rect x="0" y="470" width="933" height="730" fill="url(#fade-top)"/>
      </mask>
      <mask id="soft-sides">
        <rect x="0" y="470" width="933" height="730" fill="url(#fade-sides)"/>
      </mask>
      <linearGradient id="pyramid-light" x1="0" y1="0" x2="0" y2="1">
        <stop offset="0" stop-color="#ffffff" stop-opacity="0"/>
        <stop offset="1" stop-color="#ffffff" stop-opacity="0.45"/>
      </linearGradient>
    </defs>
    <g mask="url(#soft-edge)">
      <rect x="0" y="470" width="933" height="730" fill="url(#tricolour)" mask="url(#soft-sides)"/>
      <rect x="0" y="800" width="933" height="400" fill="url(#pyramid-light)"/>
    </g>
  </svg>

  <h1 class="title">
    <span class="title-line title-line--lead">Sous les</span>
    <span class="title-line title-line--main">Ciels Calmes</span>
  </h1>

  <svg class="flourish" viewBox="0 0 933 1200" aria-hidden="true">
    <path d="M380,440 C520,432 680,420 805,398 C830,394 820,388 790,392 C640,410 480,430 400,452"
          fill="none" stroke="var(--title-blue)" stroke-width="2.5" stroke-linecap="round"/>
  </svg>

  <p class="publisher">Editions Marvelle</p>
</main>
</body>
</html>
```